Pine Ledge Traders, LLC- Global Beverage Company with 100% Cold Chain Logistics

Hey All, My Name is Dale, I am a young business owner in a competitive export space, but my niche is that I am shipping all of my beer around the world, "100% Cold Chain". This model is more costly, but it protects the integrity of the beer itself and will give folks in foreign countries the best representation of what US Craft Beer has to offer.

I am not a branding guy and don't claim to be one, I am a salesperson first, and will be referring to all of you to create something great that will be memorable.

I am looking for a basic Business Card Design for my Craft Beer Export company. I sell US Craft Beer in several countries around the globe. Austrailia, China, Taiwan, Chile, France, New Zealand... to name a few.

I am looking for a sleek, modern, and fresh design. Quickly!

Thanks for your consideration!

Cheers,

Dale

Target Market(s)

International

Contact Information for Business Card

Dale Corrigan
Founder- Roaming Hops Guy
Dale@PineLedgeTraders.example
@RoamingHopsGuy- Instagram only
www.Pineledgetraders.example
@PineLedgeTradersAU- Instagram Only

Font styles to use
Serif

Colors
0592cd
ffffff

Requirements
Must have
• Name-
• Title-
• Email-
• Social Media Handle-
• Company Website-
Nice to have
• Nice Logo/ Images on Card
Should not have
• Tacky Beer Images

```html
<!DOCTYPE html>
<html lang="en">
<head>
<meta charset="utf-8">
<title>Pine Ledge Traders – Business Card</title>
<link rel="stylesheet" href="https://fonts.googleapis.com/css2?family=Cinzel:wght@400;600&family=Lato:wght@400;700&display=swap">
<style>
  :root {
    --brand-blue: #0592cd;
    --ink: #0d0d0d;
    --paper: #ffffff;
    --text-light: #e6e6e6;
    --divider: #3a3a3a;
    --backdrop: #2e2a27;
    --map-pale: #f3f7fd;
    --map-soft: #bcd3f0;
    --map-mid: #4f88d0;
  }
  * { box-sizing: border-box; margin: 0; padding: 0; }
  html, body { width: 1200px; height: 900px; overflow: hidden; }
  body {
    background: var(--backdrop);
    display: flex;
    align-items: center;
    justify-content: center;
    gap: 40px;
  }
  .card {
    width: 540px;
    height: 309px;
    position: relative;
    overflow: hidden;
    box-shadow: 0 10px 28px rgba(0,0,0,0.45);
  }

  /* Front */
  .card-front { background: var(--ink); }
  .company-lockup {
    position: absolute;
    left: 30px;
    top: 138px;
    width: 250px;
    display: flex;
    align-items: center;
    gap: 12px;
  }
  .company-mark {
    width: 30px; height: 30px;
    background: var(--brand-blue);
    flex: none;
  }
  .company-name {
    font-family: "Cinzel", serif;
    font-weight: 600;
    font-size: 25px;
    line-height: 1.1;
    color: var(--brand-blue);
  }
  .divider {
    position: absolute;
    left: 298px;
    top: 62px;
    width: 1px;
    height: 150px;
    background: var(--divider);
  }
  .contact {
    position: absolute;
    left: 314px;
    top: 62px;
    font-family: "Lato", sans-serif;
    color: var(--text-light);
  }
  .contact-name {
    font-family: "Cinzel", serif;
    font-weight: 600;
    font-size: 19px;
    line-height: 1.1;
    color: var(--brand-blue);
    letter-spacing: 0.5px;
  }
  .contact-title { font-size: 13px; margin: 3px 0 8px; }
  .contact-list { list-style: none; font-size: 12.5px; }
  .contact-list li {
    display: flex;
    align-items: center;
    gap: 6px;
    line-height: 1.6;
    white-space: nowrap;
  }
  .contact-list .gap { margin-top: 10px; }
  .icon { width: 10px; height: 10px; flex: none; }
  .social-dot {
    width: 10px; height: 10px;
    border-radius: 50%;
    background: var(--brand-blue);
    flex: none;
  }
  .tagline {
    position: absolute;
    left: 200px;
    bottom: 42px;
    font-family: "Cinzel", serif;
    font-size: 19px;
    color: var(--brand-blue);
    letter-spacing: 0.5px;
    white-space: nowrap;
  }

  /* Back */
  .card-back { background: var(--paper); }
  .world-map {
    position: absolute;
    left: 0; top: 0;
    width: 100%;
    height: 246px;
    background:
      linear-gradient(180deg, var(--map-pale) 0%, rgba(243,247,253,0) 18%),
      linear-gradient(90deg, var(--map-soft) 0%, var(--map-mid) 35%, var(--map-soft) 55%, var(--map-mid) 80%, var(--map-soft) 100%);
  }
  .markets-band {
    position: absolute;
    left: 0; bottom: 0;
    width: 100%;
    height: 63px;
    background: var(--ink);
    display: flex;
    align-items: center;
    padding-left: 34px;
  }
  .markets {
    font-family: "Lato", sans-serif;
    font-size: 15px;
    color: var(--brand-blue);
  }
</style>
</head>
<body>
  <section class="card card-front">
    <div class="company-lockup">
      <span class="company-mark"></span>
      <span class="company-name">Pine Ledge Traders</span>
    </div>

    <div class="divider"></div>

    <div class="contact">
      <p class="contact-name">Dale Corrigan</p>
      <p class="contact-title">Founder - Roaming Hops Guy</p>
      <ul class="contact-list">
        <li>
          <svg class="icon" viewBox="0 0 10 10"><rect x="0.5" y="1.5" width="9" height="7" fill="none" stroke="#e6e6e6"/><path d="M0.5 1.5 L5 5.5 L9.5 1.5" fill="none" stroke="#e6e6e6"/></svg>
          Dale@PineLedgeTraders.example
        </li>
        <li>
          <svg class="icon" viewBox="0 0 10 10"><circle cx="5" cy="5" r="4.3" fill="none" stroke="#e6e6e6"/><path d="M0.7 5 H9.3 M5 0.7 V9.3" stroke="#e6e6e6" stroke-width="0.8"/></svg>
          www.Pineledgetraders.example
        </li>
        <li class="gap"><span class="social-dot"></span>@RoamingHopsGuy</li>
        <li><span class="social-dot"></span>@PineLedgeTradersAU</li>
      </ul>
    </div>

    <p class="tagline">100% Cold Chain Logistics</p>
  </section>

  <section class="card card-back">
    <div class="world-map" role="img" aria-label="Dotted blue world map showing the continents on a pale background"></div>
    <div class="markets-band">
      <p class="markets">Austrailia | China | Taiwan | Chile | France | New Zealand</p>
    </div>
  </section>
</body>
</html>
```